CBD/HEMP website for e-commerce store

I need a CBD website for my shopify store. I am looking for a layout similar to these site ( https://quietmeadowcbd.com/ ) (https://elmridgecbd.com/) but with my logo and products. I am attaching what my logo looks like so that it helps with the design.

Target Market(s)

CBD HEMP CANNABIS

Industry/Entity Type

Cannabis

Coding

Coded - Design and coding required

Number of Pages Required

5+ page

Requirements
Nice to have
• I would like for it to have a trendy/galaxy feel

```html
<!DOCTYPE html>
<html lang="en">
<head>
<meta charset="utf-8">
<title>Lumora CBD</title>
<link rel="stylesheet" href="https://fonts.googleapis.com/css2?family=Karla:wght@300;400;500;700&family=Tinos:wght@400&display=swap">
<style>
:root{
  --ink:#1b1b1f;
  --muted:#555;
  --night:#1d1329;
  --blush:#fcf0f5;
  --pink:#e0257f;
  --plum:#9e1a68;
  --star:#f2b90c;
  --white:#fff;
  --sans:"Karla",Arial,sans-serif;
  --serif:"Tinos","Times New Roman",serif;
}
*{box-sizing:border-box;margin:0;padding:0}
html,body{width:1200px;height:3704px;overflow:hidden}
body{position:relative;font-family:var(--sans);color:var(--ink);background:var(--white)}
.abs{position:absolute}
.btn{position:absolute;display:flex;align-items:center;justify-content:center;background:linear-gradient(180deg,var(--pink),var(--plum));color:var(--white);font:700 15px/1 var(--sans);letter-spacing:.06em;text-transform:uppercase;text-decoration:none}
.center{left:0;width:1200px;text-align:center}

.promo-bar{top:0;left:0;width:1200px;height:34px;background:var(--night);color:var(--white);font-size:11px;letter-spacing:.05em;display:flex;align-items:center;justify-content:center}
.hero{top:34px;left:0;width:1200px;height:508px;background:
  radial-gradient(ellipse 30% 35% at 22% 30%,rgba(120,60,170,.55),transparent 70%),
  radial-gradient(ellipse 28% 30% at 80% 55%,rgba(190,70,150,.45),transparent 70%),
  radial-gradient(ellipse 40% 30% at 50% 70%,rgba(90,50,150,.5),transparent 75%),
  radial-gradient(ellipse at 50% 40%,#4a2468 0%,#27133f 50%,#0f0920 100%)}
.hero-buds{top:420px;left:0;width:1200px;height:122px;background:
  radial-gradient(ellipse 9% 60% at 5% 100%,#6f8a2c,transparent 70%),
  radial-gradient(ellipse 10% 70% at 22% 100%,#7f9a34,transparent 70%),
  radial-gradient(ellipse 9% 65% at 38% 100%,#6f8a2c,transparent 70%),
  radial-gradient(ellipse 10% 75% at 55% 100%,#839f36,transparent 70%),
  radial-gradient(ellipse 9% 65% at 72% 100%,#6f8a2c,transparent 70%),
  radial-gradient(ellipse 10% 70% at 90% 100%,#7f9a34,transparent 70%),
  linear-gradient(180deg,transparent 45%,#58701f 80%,#4a5e1a 100%)}
.nav{top:72px;font-size:11px;letter-spacing:.06em;color:var(--white);text-transform:uppercase}
.brand{top:58px;left:490px;width:220px;text-align:center;font:700 36px/1 var(--sans);letter-spacing:.12em;color:var(--white)}
.hero-title{color:var(--white)}
.chev{top:276px}

.reviews{top:542px;left:0;width:1200px;height:270px;background:var(--blush)}
.section-label{font:700 17px/1 var(--sans);letter-spacing:.04em;text-transform:uppercase}
.review{position:absolute;top:94px;width:235px}
.stars{color:var(--star);font-size:11px;letter-spacing:1px}
.review-date{font-size:12px;margin-left:6px}
.review-quote{font:14px/1 var(--serif);margin-top:12px}
.review-thumb{position:absolute;top:54px;left:0;width:42px;height:42px;background:radial-gradient(circle,#8e8a3a 0%,#b9a65a 40%,#f6f1e6 72%)}
.review-text{position:absolute;top:54px;left:50px;font-size:9.5px;line-height:14.5px;color:var(--muted);white-space:nowrap}
.review-strain{position:absolute;top:103px;left:0;font-size:7px;color:var(--muted)}
.review-author{position:absolute;top:120px;left:50px;font-size:10px;font-weight:700}

.product{position:absolute;top:999px;width:240px}
.product-photo{width:240px;height:304px;background:
  radial-gradient(ellipse 36% 26% at 50% 50%,#7d8c4a 0%,#a7b27a 45%,rgba(253,246,249,0) 100%),#fdf6f9}
.product-name{font:16px/1 var(--serif);margin-top:14px}
.product-price{font-size:11px;margin-top:6px}
.product-rating{font-size:8px;margin-top:4px;color:var(--muted)}

.categories{top:1505px;left:0;width:1200px;height:587px;background:var(--blush)}
.tile{position:absolute;top:61px;width:378px;height:499px}
.tile-label{position:absolute;left:29px;top:370px;color:var(--white);font:700 13px/1 var(--sans)}
.tile-name{position:absolute;left:29px;top:387px;color:var(--white);font:36px/1 var(--serif)}
.tile .btn{left:29px;top:435px;width:117px;height:35px;font-size:13px}

.plugged{top:2092px;left:0;width:1200px;height:503px;background:
  radial-gradient(ellipse 22% 30% at 50% 22%,rgba(235,150,220,.75),transparent 70%),
  radial-gradient(ellipse 35% 45% at 50% 30%,rgba(140,70,170,.6),transparent 75%),
  radial-gradient(ellipse 60% 18% at 50% 98%,rgba(150,170,230,.55),transparent 75%),
  linear-gradient(180deg,#15163f 0%,#1d1f58 55%,#2a3478 85%,#121534 100%)}
.plugged-text{font-size:16px;line-height:26.5px;color:#e8e4f5}

.blog{top:2595px;left:0;width:1200px;height:717px;background:var(--blush)}
.post{position:absolute;top:188px;width:326px}
.post-photo{width:326px;height:206px}
.post-title{font:17px/23px var(--serif);margin-top:12px;white-space:nowrap}
.post-text{font-size:11.5px;line-height:19px;color:var(--muted);margin-top:7px;white-space:nowrap}
.post-more{font-size:10.5px;font-weight:700;letter-spacing:.05em;color:var(--muted);margin-top:10px}

.footer{top:3312px;left:0;width:1200px;height:392px;background:var(--night);color:var(--white)}
.footer-title{font:700 15px/1 var(--sans);letter-spacing:.04em}
.footer-text{font-size:13px;line-height:22px;white-space:nowrap}
.footer-menu{font-size:12.5px;line-height:25px;list-style:none}
.email-field{position:absolute;left:818px;top:151px;width:282px;height:42px;border:1px solid #cfc8d6;font-size:12px;padding:0 12px;display:flex;align-items:center}
.social{display:inline-block;width:10px;height:10px;border-radius:50%;background:var(--white);margin-right:9px}
</style>
</head>
<body>

<div class="abs promo-bar">FREE SHIPPING ON ALL ORDERS OVER $99</div>

<section class="abs hero" role="img" aria-label="Purple starry galaxy sky with pink nebula glow"></section>
<div class="abs hero-buds" role="img" aria-label="Row of green cannabis buds along the bottom of the sky"></div>
<nav>
  <span class="abs nav" style="left:99px">Shop</span>
  <span class="abs nav" style="left:162px">Reviews</span>
  <span class="abs nav" style="left:245px">Blog</span>
  <span class="abs nav" style="left:307px">Our Story</span>
  <span class="abs nav" style="left:401px">Wholesale</span>
  <div class="abs brand">LUMORA</div>
  <span class="abs nav" style="left:888px">Account</span>
  <span class="abs nav" style="left:974px">Search</span>
  <span class="abs nav" style="left:1053px">Cart (0)</span>
</nav>
<svg class="abs chev" style="left:70px" width="14" height="28" viewBox="0 0 14 28"><path d="M12 2 2 14l10 12" fill="none" stroke="#fff" stroke-width="1.5"/></svg>
<svg class="abs chev" style="left:1113px" width="14" height="28" viewBox="0 0 14 28"><path d="M2 2l10 12L2 26" fill="none" stroke="#fff" stroke-width="1.5"/></svg>
<h1 class="abs center hero-title" style="top:226px;font:400 52px/1 var(--serif)">THE ULTIMATE</h1>
<p class="abs center hero-title" style="top:282px;font:400 40px/1 var(--sans);letter-spacing:.05em">CANNABIS EXPERIENCE</p>
<a class="btn" style="left:533px;top:340px;width:134px;height:41px">Shop Now</a>

<section class="abs reviews">
  <h2 class="abs section-label" style="left:98px;top:49px">Real Reviews From Real Customers</h2>
  <svg class="abs" style="left:1070px;top:48px" width="30" height="18" viewBox="0 0 30 18"><path d="M8 2 2 9l6 7M22 2l6 7-6 7" fill="none" stroke="#222" stroke-width="1.5"/></svg>
  <div class="review" style="left:98px"><span class="stars">★★★★★</span><span class="review-date">25/12/2020</span><p class="review-quote">I would definitely recommend this</p><div class="review-thumb" role="img" aria-label="Cannabis flower"></div><p class="review-text">Lorem ipsum d consectetur adipiscing<br>elit, sed do eiusmod tempor incididunt<br>ut labore et dolore magna aliqua. Quis<br>ipsum suspendisse ultrices</p><span class="review-strain">Meadow OG</span><span class="review-author">-Jane Rowe</span></div>
  <div class="review" style="left:356px"><span class="stars">★★★★★</span><span class="review-date">25/12/2020</span><p class="review-quote">I would definitely recommend this</p><div class="review-thumb" role="img" aria-label="Cannabis flower"></div><p class="review-text">Lorem ipsum d consectetur adipiscing<br>elit, sed do eiusmod tempor incididunt<br>ut labore et dolore magna aliqua. Quis<br>ipsum suspendisse ultrices</p><span class="review-strain">Meadow OG</span><span class="review-author">-Jane Rowe</span></div>
  <div class="review" style="left:614px"><span class="stars">★★★★★</span><span class="review-date">25/12/2020</span><p class="review-quote">I would definitely recommend this</p><div class="review-thumb" role="img" aria-label="CBD oil bottle" style="background:radial-gradient(ellipse 22% 45% at 50% 55%,#b89a22,#e3d48a 60%,#f6f1e6 100%)"></div><p class="review-text">Lorem ipsum d consectetur adipiscing<br>elit, sed do eiusmod tempor incididunt<br>ut labore et dolore magna aliqua. Quis<br>ipsum suspendisse ultrices</p><span class="review-strain">Meadow OG</span><span class="review-author">-Jane Rowe</span></div>
  <div class="review" style="left:871px"><span class="stars">★★★★★</span><span class="review-date">25/12/2020</span><p class="review-quote">I would definitely recommend this</p><div class="review-thumb" role="img" aria-label="Cannabis flower"></div><p class="review-text">Lorem ipsum d consectetur adipiscing<br>elit, sed do eiusmod tempor incididunt<br>ut labore et dolore magna aliqua. Quis<br>ipsum suspendisse ultrices</p><span class="review-strain">Meadow OG</span><span class="review-author">-Jane Rowe</span></div>
</section>

<p class="abs center" style="top:904px;font-size:15px;letter-spacing:.03em">POPULAR TODAY</p>
<h2 class="abs center" style="top:928px;font:46px/1 var(--serif)">CBD PRODUCTS</h2>
<div class="product" style="left:98px"><div class="product-photo" role="img" aria-label="Cannabis flower bud"></div><p class="product-name">Product Name</p><p class="product-price">Starting at $32</p><p class="product-rating"><span class="stars" style="font-size:8px">★★★★★</span> 269 Reviews</p></div>
<div class="product" style="left:352px"><div class="product-photo" role="img" aria-label="Long cannabis flower bud" style="background:radial-gradient(ellipse 18% 36% at 50% 48%,#7d8c4a 0%,#a7b27a 45%,rgba(253,246,249,0) 100%),#fdf6f9"></div><p class="product-name">Product Name</p><p class="product-price">Starting at $32</p><p class="product-rating"><span class="stars" style="font-size:8px">★★★★★</span> 269 Reviews</p></div>
<div class="product" style="left:606px"><div class="product-photo" role="img" aria-label="CBD oil dropper bottle" style="background:radial-gradient(ellipse 17% 36% at 50% 55%,#c4a422 0%,#d8c46a 55%,rgba(253,246,249,0) 100%),#fdf6f9"></div><p class="product-name">Product Name</p><p class="product-price">Starting at $32</p><p class="product-rating"><span class="stars" style="font-size:8px">★★★★★</span> 269 Reviews</p></div>
<div class="product" style="left:860px"><div class="product-photo" role="img" aria-label="Cannabis flower bud"></div><p class="product-name">Product Name</p><p class="product-price">Starting at $32</p><p class="product-rating"><span class="stars" style="font-size:8px">★★★★★</span> 269 Reviews</p></div>
<a class="btn" style="left:533px;top:1402px;width:134px;height:41px">Shop Now</a>

<section class="abs categories">
  <div class="tile" style="left:24px;background:radial-gradient(ellipse 60% 50% at 50% 35%,#7c8a66,#3a4232 55%,#111310 100%)" role="img" aria-label="Cannabis plant close up">
    <span class="tile-label">CBD</span><span class="tile-name">Flowers</span><a class="btn">Shop Now</a></div>
  <div class="tile" style="left:411px;background:radial-gradient(ellipse 42% 32% at 50% 28%,#eef0f4,#9cc4dc 70%,transparent 100%),linear-gradient(180deg,#a892b6,#c49a9a 70%,#b07c86)" role="img" aria-label="Hands holding a blue and white bath bomb">
    <span class="tile-label">CBD</span><span class="tile-name">Bath Bombs</span><a class="btn">Shop Now</a></div>
  <div class="tile" style="left:797px;background:linear-gradient(90deg,#7a3a24 0%,#d8a88c 40%,#c8a08a 60%,#8ea060 100%)" role="img" aria-label="Young woman holding a vape pen outdoors">
    <span class="tile-label">CBD</span><span class="tile-name">Vapes</span><a class="btn">Shop Now</a></div>
</section>

<section class="abs plugged" role="img" aria-label="Starry night sky over a misty forest with a glowing cannabis leaf"></section>
<svg class="abs" style="left:354px;top:2092px" width="500" height="503" viewBox="0 0 500 503"><circle cx="250" cy="250" r="245" fill="none" stroke="#f4eefc" stroke-width="3" opacity=".9"/></svg>
<h2 class="abs center" style="top:2340px;font:42px/1 var(--serif);color:var(--white)">GET PLUGGED IN</h2>
<p class="abs center plugged-text" style="top:2388px">Lorem ipsum dolor sit amet, consectetur adipiscing elit, sed do eiusmod tempor incididunt<br>ut labore et dolore magna aliqua. Quis ipsum suspendisse ultrices gravida. Risus commodo<br>viverra maecenas accumsan lacus vel facilisis.</p>
<a class="btn" style="left:533px;top:2484px;width:134px;height:38px">Shop Now</a>

<section class="abs blog">
  <p class="abs center" style="top:90px;font-size:15px;letter-spacing:.03em">BLOG</p>
  <h2 class="abs center" style="top:112px;font:44px/1 var(--serif)">Shared Secrets</h2>
  <article class="post" style="left:99px"><div class="post-photo" role="img" aria-label="Hands rolling cannabis on a table" style="background:radial-gradient(ellipse 30% 35% at 45% 50%,#4c5228,transparent 80%),#e4ded6"></div><h3 class="post-title">Lorem ipsum dolor sit amctetur adipiscing<br>elit, sed do eiusmod tempor</h3><p class="post-text">Lorem ipsum dolor sit amet, consectetur adipiing elit,<br>sed do eiusmod tempor incididunt ut labore et dolore<br>magna aliqua. Quis ipsum suspendisse</p><p class="post-more">READ MORE ⟶</p></article>
  <article class="post" style="left:437px"><div class="post-photo" role="img" aria-label="Chocolate cookie with cannabis leaf" style="background:radial-gradient(ellipse 24% 40% at 68% 42%,#5a3a26,transparent 85%),linear-gradient(180deg,#eceae4 0%,#9aa66a 55%,#8a6a4e 100%)"></div><h3 class="post-title">Lorem ipsum dolor sit amctetur adipiscing<br>elit, sed do eiusmod tempor</h3><p class="post-text">Lorem ipsum dolor sit amet, consectetur adipiing elit,<br>sed do eiusmod tempor incididunt ut labore et dolore<br>magna aliqua. Quis ipsum suspendisse</p><p class="post-more">READ MORE ⟶</p></article>
  <article class="post" style="left:775px"><div class="post-photo" role="img" aria-label="Person lighting a joint" style="background:radial-gradient(ellipse 35% 50% at 65% 60%,#d4a08a,transparent 80%),linear-gradient(135deg,#164e50,#3e9294 60%,#1f5c5e)"></div><h3 class="post-title">Lorem ipsum dolor sit amctetur adipiscing<br>elit, sed do eiusmod tempor</h3><p class="post-text">Lorem ipsum dolor sit amet, consectetur adipiing elit,<br>sed do eiusmod tempor incididunt ut labore et dolore<br>magna aliqua. Quis ipsum suspendisse</p><p class="post-more">READ MORE ⟶</p></article>
  <a class="btn" style="left:519px;top:585px;width:162px;height:40px">View All Posts</a>
</section>

<footer class="abs footer">
  <h4 class="abs footer-title" style="left:98px;top:57px">ABOUT THE SHOP</h4>
  <p class="abs footer-text" style="left:98px;top:84px">Lorem ipsum dolor sit amet, coctetur adipiscing<br>elit, sed do eiusmod tempor incididunt</p>
  <p class="abs footer-text" style="left:98px;top:142px">Lorem ipsum dolor sit amet, consecur adipiscing<br>elit, sed do eiusmod tempor incididunt ut labore<br>et dolore magna aliqua.</p>
  <p class="abs footer-text" style="left:98px;top:222px"><svg width="12" height="10" viewBox="0 0 12 10" style="margin-right:6px"><rect x=".5" y=".5" width="11" height="9" fill="none" stroke="#fff"/><path d="M.5 .5 6 5l5.5-4.5" fill="none" stroke="#fff"/></svg>info@lumoracbd.com</p>
  <p class="abs footer-text" style="left:98px;top:256px"><svg width="11" height="11" viewBox="0 0 24 24" style="margin-right:6px"><path fill="#fff" d="M6.6 10.8a15 15 0 0 0 6.6 6.6l2.2-2.2a1 1 0 0 1 1-.25 11.4 11.4 0 0 0 3.6.57 1 1 0 0 1 1 1V20a1 1 0 0 1-1 1A17 17 0 0 1 3 4a1 1 0 0 1 1-1h3.5a1 1 0 0 1 1 1c0 1.25.2 2.45.57 3.57a1 1 0 0 1-.25 1z"/></svg>Call &amp; Text : 555 010 0199</p>
  <div class="abs" style="left:98px;top:294px"><span class="social"></span><span class="social"></span><span class="social"></span><span class="social"></span></div>

  <h4 class="abs footer-title" style="left:543px;top:57px">MENU</h4>
  <ul class="abs footer-menu" style="left:543px;top:82px">
    <li>About Us</li><li>Terms &amp; Conditions</li><li>Shipping &amp; Returns</li><li>Privacy Policy</li><li>Disclaimer</li><li>Contact us</li><li>CBD Flower Wholesale</li><li>CBD HEMP F.A.Q</li><li>CBD / Hemp Lab Tests</li>
  </ul>

  <h4 class="abs footer-title" style="left:812px;top:57px">GET THE DROP</h4>
  <p class="abs footer-text" style="left:812px;top:84px;line-height:25px">Join our newsletter and get updated on<br>new products, strains, and merch.</p>
  <div class="email-field">Enter your Email address</div>
  <a class="btn" style="left:968px;top:203px;width:132px;height:42px">Subscribe</a>

  <div class="abs" style="left:98px;top:341px;width:1002px;height:1px;background:#3c3148"></div>
  <p class="abs center" style="top:358px;font-size:13px">2020 LUMORA. All Rights Reserved.</p>
</footer>

</body>
</html>
```